COVER ONLY - Electrical supply company needs new catalogue cover (front and back)

We're currently finalising our catalogue and have gone through many changes in branding since our last catalogue so need a completely NEW design incorporating the new logo and design feel from the CI document attached.

Since the company is moving more corporate we'd like a much cleaner looking cover (front and back) from what we had before. We'd would like to keep a dominate color for the year so we can simply change the color for the following year catalogue.

We'd like to show product images (supplied) on the front of the catalogue but not as dominate as our previous catalogue (attached to get an idea of where we came from).

We'd like to introduce as much of our new CI into the new catalogue cover as possible while keeping up with our new corporate style of "clean and neat".

I've attached our logo, CI guide, old catalogue cover and some product images.

We would like the file to be handed over in complete format as well as in .psd

(Our website is also being updated but the old website is still up www.qv.co.za)
Updates

Cover size is A4 and the spine will be roughly 3/4 inch.

Please make sure you read the CI guide.

Produce something that shows professionalism, class and style.  We want something that any multi national billion dollar company would be proud to show

Industry/Entity Type

Electrical

Font styles to use
Other font styles liked:
• Sansation

```html
<!DOCTYPE html>
<html lang="en">
<head>
<meta charset="utf-8">
<title>QuantaVolt Catalogue Cover</title>
<link rel="stylesheet" href="https://fonts.googleapis.com/css2?family=Open+Sans:wght@400;600;700&display=swap">
<style>
  :root{
    --backdrop:#e6e6e8;
    --paper:#ffffff;
    --teal:#3fb4c6;
    --teal-pale:#bfe6ee;
    --grey:#9c9c9f;
    --charcoal:#3a3a3d;
    --ink:#3c3c3e;
    --sky-top:#1f5fb3;
    --sky-bottom:#8fc3e8;
    --map:#dcecf6;
  }
  *{box-sizing:border-box;margin:0;padding:0}
  html,body{width:1200px;height:683px;overflow:hidden;background:var(--backdrop);font-family:"Open Sans",sans-serif}
  .spread{position:absolute;left:170px;top:38px;width:860px;height:608px;box-shadow:0 6px 22px rgba(0,0,0,.18)}
  .page{position:absolute;top:0;width:430px;height:608px;background:var(--paper);overflow:hidden}
  .page--back{left:0}
  .page--front{left:430px}
  .page svg.art{position:absolute;inset:0}
  .wordmark{position:absolute;display:flex;align-items:center;gap:6px;color:var(--teal);font-weight:600;font-size:17px;letter-spacing:.3px}
  .wordmark .mark-square{width:11px;height:11px;background:var(--teal)}
  .page--back .wordmark{left:28px;top:40px}
  .page--front .wordmark{left:26px;top:20px}

  .range{position:absolute;left:28px;top:76px;width:385px;color:var(--ink);font-size:8.6px;line-height:1.38}
  .range h2{font-size:10.5px;font-weight:700;margin:6px 0 3px}
  .range p{margin:0}
  .range .group{margin-top:7px}
  .range .brands{margin-top:5px}

  .contact-title{position:absolute;left:150px;top:434px;color:#eef6f8;font-size:22px;font-weight:600;letter-spacing:.5px}
  .contact-durban{position:absolute;left:270px;top:426px;color:#fff;font-size:10.5px;line-height:1.35}
  .contact-cape{position:absolute;left:70px;top:520px;color:#fff;font-size:11px;line-height:1.35}

  .tagline{position:absolute;left:24px;top:72px;width:200px;color:#fff;font-size:15px;line-height:1.22;font-weight:400}
  .web{position:absolute;right:24px;bottom:40px;color:#fff;font-size:11px;font-weight:600;letter-spacing:.4px}
</style>
</head>
<body>
<main class="spread">

  <section class="page page--back" aria-label="Back cover">
    <svg class="art" viewBox="0 0 430 608" width="430" height="608" aria-hidden="false">
      <rect class="world-map" role="img" aria-label="Faint world map behind the product range" x="60" y="50" width="360" height="380" rx="60" fill="var(--map)" opacity=".75"/>
      <path d="M0 392 Q215 372 430 408 L430 608 L0 608Z" fill="var(--grey)"/>
      <path d="M0 422 Q215 402 430 440 L430 608 L0 608Z" fill="var(--teal)"/>
      <path d="M0 478 Q215 456 430 496 L430 608 L0 608Z" fill="var(--charcoal)"/>
    </svg>

    <div class="wordmark"><span class="mark-square"></span>QuantaVolt</div>

    <div class="range">
      <h2>A : relays</h2>
      <p>PCB, plug-in, step, miniature industrial and power relays; relay interface modules; sockets; daylight switches; solid-state relays and accessories</p>
      <p class="brands">Brands: Ferrin, Corvant</p>

      <h2>B : motor control</h2>
      <div class="group">
        <p>Control and protection</p>
        <p>• Contactors • Semi-conductor contactors • Thermal overload relays</p>
        <p>• Motor control circuit breakers • Motor starters • Soft starters</p>
        <p>• IC soft starters • Electronic motor protection</p>
      </div>
      <div class="group">
        <p>Command and signalling</p>
        <p>• Pushbuttons and selectors • Signal towers and beacons</p>
        <p>• Limit and foot switches • Rotary cam switches</p>
        <p>• Joystick controls • Pendant controls • Wormgear limit switches</p>
      </div>
      <div class="group">
        <p>Switching and circuit protection</p>
        <p>• Load break switches • Earth leakage relays</p>
      </div>
      <div class="group">
        <p>Automation and control</p>
        <p>• Time relays • Protection relays • Level control relays</p>
        <p>• Programmable logic relays • Switching power supplies</p>
      </div>
      <div class="group">
        <p>Energy management</p>
        <p>• Metering instruments (kwh) • Automatic power factor controllers</p>
        <p>• Automatic battery chargers • Automatic transfer switch controllers</p>
        <p>• Engine and generator controllers</p>
      </div>
      <p class="brands">Brands: Lunaro, Tessa, Falcor, IQ Circuit</p>
    </div>

    <div class="contact-title">Contact</div>
    <address class="contact-durban" style="font-style:normal">
      7400 P.O. Box 20418<br>Bayhead<br>4001 Durban<br>
      Telephone: 011 555 0140<br>Telefax: 011 555 0188<br>Email: info@qv.co.za
    </address>
    <address class="contact-cape" style="font-style:normal">
      Cape Province<br>14 Ridgeview Office Park<br>Harbour Road<br>Milton Flats<br>Cape Town
    </address>
  </section>

  <section class="page page--front" aria-label="Front cover">
    <svg class="art" viewBox="0 0 430 608" width="430" height="608">
      <defs>
        <linearGradient id="sky" x1="0" y1="0" x2="0.3" y2="1">
          <stop offset="0" stop-color="var(--sky-top)"/>
          <stop offset="1" stop-color="var(--sky-bottom)"/>
        </linearGradient>
        <linearGradient id="products" x1="0" y1="0" x2="1" y2="1">
          <stop offset="0" stop-color="#4a4d55"/>
          <stop offset=".55" stop-color="#9aa3ad"/>
          <stop offset="1" stop-color="#dfe4e8"/>
        </linearGradient>
      </defs>
      <path role="img" aria-label="Photograph of blue sky crossed by power lines" d="M0 58 Q215 44 430 56 L430 360 Q215 330 0 380Z" fill="url(#sky)"/>
      <path d="M60 330 Q60 200 200 190 L430 176 L430 420 Q215 390 60 430Z" fill="var(--teal-pale)" opacity=".85"/>
      <rect role="img" aria-label="Photograph of products: drive, circuit breaker, controller and isolator switch" x="140" y="200" width="270" height="190" rx="14" fill="url(#products)"/>
      <path d="M0 400 Q215 360 430 400 L430 608 L0 608Z" fill="var(--grey)"/>
      <path d="M0 430 Q215 392 430 432 L430 608 L0 608Z" fill="var(--teal)"/>
      <path d="M0 470 Q215 430 430 470 L430 608 L0 608Z" fill="var(--charcoal)"/>
    </svg>

    <div class="wordmark"><span class="mark-square"></span>QuantaVolt</div>
    <p class="tagline">Dedicated suppliers of quality products &amp; service at competitive prices</p>
    <div class="web">www.qv.co.za</div>
  </section>

</main>
</body>
</html>
```